Corbell Lending Partners - Real estate loans - need a business card with a logo

I need a logo and a business card that looks elegant - that looks as if it is a big stablish corporation - We do real estate loans, my goal is to brand myself with colors black background - gold or silver letters - some combination - Name of the company different color than the rest of the card -

```html
<!DOCTYPE html>
<html lang="en">
<head>
<meta charset="UTF-8">
<title>Corbell Lending Partners – Business Card</title>
<link href="https://fonts.googleapis.com/css2?family=Montserrat:wght@400;500;700&display=swap" rel="stylesheet">
<style>
  :root {
    --backdrop: #262626;
    --card: #1b1b1b;
    --gold: #d8b987;
    --silver: #f1f1f1;
  }
  * { margin: 0; padding: 0; box-sizing: border-box; }
  html, body {
    width: 1200px;
    height: 900px;
    overflow: hidden;
    background: var(--backdrop);
    font-family: "Montserrat", sans-serif;
  }
  .stage {
    width: 1200px;
    height: 900px;
    display: flex;
    flex-direction: column;
    align-items: center;
    justify-content: center;
    gap: 40px;
  }
  .card {
    position: relative;
    width: 700px;
    height: 400px;
    background: var(--card);
    box-shadow: 0 10px 30px rgba(0,0,0,0.45);
  }
  .brand {
    display: flex;
    align-items: center;
    gap: 14px;
    color: var(--gold);
    font-weight: 700;
    white-space: nowrap;
  }
  .brand-mark {
    background: var(--gold);
    flex: none;
  }
  .card-front .brand {
    position: absolute;
    top: 50%;
    left: 50%;
    transform: translate(-50%, -50%);
    font-size: 38px;
  }
  .card-front .brand-mark { width: 30px; height: 30px; }
  .card-back .brand {
    position: absolute;
    top: 50px;
    left: 50px;
    font-size: 24px;
    gap: 10px;
  }
  .card-back .brand-mark { width: 20px; height: 20px; }
  .website {
    position: absolute;
    left: 50px;
    bottom: 55px;
    color: var(--gold);
    font-weight: 500;
    font-size: 17px;
    letter-spacing: 0.3px;
  }
  .contact {
    position: absolute;
    left: 400px;
    top: 180px;
    color: var(--silver);
    font-size: 17px;
    line-height: 1.35;
  }
  .contact-name {
    color: var(--gold);
    font-size: 25px;
    font-weight: 500;
    letter-spacing: 0.5px;
  }
  .contact-title { margin-bottom: 26px; }
  .contact-lines { margin-bottom: 26px; }
</style>
</head>
<body>
  <main class="stage">
    <section class="card card-front" aria-label="Card front">
      <div class="brand"><span class="brand-mark"></span>Corbell Lending Partners</div>
    </section>

    <section class="card card-back" aria-label="Card back">
      <div class="brand"><span class="brand-mark"></span>Corbell Lending Partners</div>
      <div class="website">www.corbelllending.com</div>
      <div class="contact">
        <div class="contact-name">Daniel Whitmore</div>
        <div class="contact-title">Director</div>
        <div class="contact-lines">
          <div>(555) 214-3870</div>
          <div>info@corbelllending.com</div>
        </div>
        <address style="font-style: normal;">
          <div>1187 Larkspur Lane</div>
          <div>Salem, OR 97301</div>
        </address>
      </div>
    </section>
  </main>
</body>
</html>
```